Parcelwise HQ letterhead and envelope

Design a formal (8.5x11) letterhead and envelope for sales outreach and legal matters. Using design input from https://www.parcelwisehq.example/ and the attached documents.

Industry/Entity Type

Software Service

Requirements
Must have
• These 4 hex colors are our official colors:
• #355c98 [blue]
• #1eb1a2 [teal]
• #fdba12 [gold]
• #f1653b [orange]
• So no other colors besides these should be used.

```html
<!DOCTYPE html>
<html lang="en">
<head>
<meta charset="utf-8">
<title>Parcelwise HQ – Letterhead and Envelope</title>
<link href="https://fonts.googleapis.com/css2?family=Open+Sans:wght@400;600;700&display=swap" rel="stylesheet">
<style>
  :root {
    --brand-blue: #355c98;
    --ink: #3a3a3a;
    --ink-soft: #555555;
    --paper: #f9f9f9;
    --rule: #6b6b6b;
    --stage: #e4e4e4;
  }
  * { box-sizing: border-box; margin: 0; padding: 0; }
  html, body {
    width: 1200px; height: 825px; overflow: hidden;
    background: var(--stage);
    font-family: "Open Sans", Arial, sans-serif;
  }
  .canvas { position: relative; width: 1200px; height: 825px; }

  /* Brand name block */
  .brand { position: absolute; display: flex; align-items: center; gap: 7px; }
  .brand-dot {
    width: 24px; height: 24px; border-radius: 50%;
    background: var(--brand-blue);
  }
  .brand-name {
    font-size: 19px; font-weight: 400; color: var(--brand-blue);
    letter-spacing: 0.2px; white-space: nowrap;
  }

  /* Letterhead */
  .letterhead {
    position: absolute; left: 81px; top: 83px;
    width: 465px; height: 658px; background: var(--paper);
  }
  .letterhead .brand { left: 36px; top: 112px; top: 29px; }
  .contact {
    position: absolute; left: 333px; top: 22px;
    font-size: 7.4px; line-height: 11.5px; color: var(--ink-soft);
  }
  .contact-item { display: flex; align-items: center; gap: 2px; }
  .contact-item svg { width: 6px; height: 6px; fill: var(--brand-blue); }
  .letter-body {
    position: absolute; left: 40px; top: 152px; width: 390px;
    color: var(--ink);
  }
  .salutation {
    font-family: Arial, "Open Sans", sans-serif;
    font-weight: 700; font-size: 10.6px; margin-bottom: 14px;
  }
  .letter-body p {
    font-size: 9.3px; line-height: 12.2px; text-align: justify;
    margin-bottom: 12px;
  }
  .signature {
    position: absolute; left: 40px; top: 467px; width: 90px; height: 42px;
    background: linear-gradient(90deg, #dcdcdc, #cfcfcf);
    border-radius: 20px;
  }
  .footer-rule {
    position: absolute; left: 0; right: 0; top: 642px;
    border-top: 0.8px solid var(--rule);
  }
  .footer-url {
    position: absolute; right: 33px; top: 636px;
    padding: 0 4px; background: var(--paper);
    font-size: 8.6px; letter-spacing: 1px; color: var(--brand-blue);
  }
  .footer-band {
    position: absolute; left: 0; right: 0; bottom: 0; height: 11px;
    background: var(--brand-blue);
  }

  /* Envelope */
  .envelope-front {
    position: absolute; left: 586px; top: 264px;
    width: 535px; height: 232px; background: var(--paper);
  }
  .envelope-front .brand { left: 34px; top: 20px; }
  .return-address {
    position: absolute; left: 38px; top: 198px;
    display: flex; align-items: center; gap: 4px;
    font-size: 8.2px; color: var(--ink);
  }
  .return-address svg { width: 7px; height: 10px; fill: var(--brand-blue); }
  .envelope-front .footer-rule { top: 214px; }
  .envelope-front .footer-url { right: 34px; top: 208px; }
  .envelope-front .footer-band { height: 10px; }
  .envelope-back {
    position: absolute; left: 586px; top: 510px;
    width: 535px; height: 231px; background: var(--paper);
  }
  .flap { position: absolute; left: 0; top: 0; width: 535px; height: 67px; }
  .flap path { fill: var(--brand-blue); }
</style>
</head>
<body>
<main class="canvas">

  <section class="letterhead" aria-label="Letterhead">
    <div class="brand">
      <span class="brand-dot"></span>
      <span class="brand-name">Parcelwise HQ</span>
    </div>

    <address class="contact" style="font-style:normal">
      <div>42 Lantern Row</div>
      <div>Brookvale, MI 48000</div>
      <div class="contact-item">
        <svg viewBox="0 0 10 10"><path d="M2 0.5 L3.8 0.5 L4.5 3 L3.3 4 Q4.3 6 6 6.8 L7 5.6 L9.5 6.3 L9.5 8.2 Q9.5 9.5 8 9.5 Q1 8.5 0.5 2 Q0.5 0.5 2 0.5Z"/></svg>
        (800) 555-0142
      </div>
      <div class="contact-item">
        <svg viewBox="0 0 10 10"><path d="M0.5 2 H9.5 V8 H0.5Z M0.5 2 L5 5.5 L9.5 2" /></svg>
        jsmith@parcelwisehq.example
      </div>
    </address>

    <div class="letter-body">
      <div class="salutation">Dear Mr. Avery,</div>
      <p>Lorem Ipsum is simply dummy text of the printing and typesetting industry. Lorem Ipsum has been the industry's standard dummy text ever since the 1500s, when an unknown printer took a galley of type and scrambled it to make a type specimen book. It has survived not only five centuries, but also the leap into electronic typesetting, remaining essentially unchanged.</p>
      <p>The standard chunk of Lorem Ipsum used since the 1500s is reproduced below for those interested. Sections 1.10.32 and 1.10.33 from "de Finibus Bonorum et Malorum" by Lucius Venn are also reproduced in their exact original form, accompanied by English versions from the 1914 translation by H. Ravell</p>
      <p>Lorem Ipsum is simply dummy text of the printing and typesetting industry. Lorem Ipsum has been the industry's standard dummy text ever since the 1500s, when an unknown printer took a galley of type and scrambled it to make a type specimen book. It has survived not only five centuries, but also the leap into electronic typesetting, remaining essentially unchanged. It was popularised in the</p>
      <p>The standard chunk of Lorem Ipsum used since the 1500s is reproduced below for those interested. Sections 1.10.32 and 1.10.33 from "de Finibus Bonorum et Malorum" by Lucius Venn are also reproduced in their exact original form, accompanied by English versions from the 1914 translation by H. Ravell</p>
    </div>

    <div class="signature" role="img" aria-label="Handwritten signature of the sender"></div>

    <div class="footer-rule"></div>
    <div class="footer-url">www.parcelwisehq.example</div>
    <div class="footer-band"></div>
  </section>

  <section class="envelope-front" aria-label="Envelope front">
    <div class="brand">
      <span class="brand-dot"></span>
      <span class="brand-name">Parcelwise HQ</span>
    </div>
    <div class="return-address">
      <svg viewBox="0 0 10 14"><path d="M5 0 A5 5 0 0 1 10 5 Q10 8 5 14 Q0 8 0 5 A5 5 0 0 1 5 0Z M5 3 A2 2 0 1 0 5.01 3Z"/></svg>
      42 Lantern Row Brookvale, MI 48000
    </div>
    <div class="footer-rule"></div>
    <div class="footer-url">www.parcelwisehq.example</div>
    <div class="footer-band"></div>
  </section>

  <section class="envelope-back" aria-label="Envelope back with flap">
    <svg class="flap" viewBox="0 0 535 67" preserveAspectRatio="none">
      <path d="M0 0 H535 Q532 22 515 28 Q420 42 300 62 Q267 69 234 62 Q110 42 20 28 Q4 22 0 0Z"/>
    </svg>
  </section>

</main>
</body>
</html>
```